Carpentry framing business card and logo design

We need a logo that works well with baseball caps, tee shirts and sweat shirts. We are a carpentry framing company specializing in apartment complexes and large residential communities. We work in what is known as the tri state area southeastern Pennsylvania , New Jersey and northern Delaware . We would like to see die signs using the old English letter M and royal blue colors. Also we stress OSHA compliance and safety.

Industry/Entity Type

Residential

Contact Information for Business Card

Valdrick Construction Co Inc
4870 Quillford Lane
Ambler PA 19087
Dale Valdrick
dale1valdrick@norvexmail.com
267-815-0926

```html
<!DOCTYPE html>
<html lang="en">
<head>
<meta charset="utf-8">
<title>Valdrick Construction Co Inc – Business Card</title>
<link rel="stylesheet" href="https://fonts.googleapis.com/css2?family=Roboto:wght@300;400&display=swap">
<style>
  :root {
    --backdrop: #e9e7e3;
    --card-white: #ffffff;
    --ink: #2a2a2a;
    --ink-soft: #555a60;
    --accent-blue: #4f7fc6;
    --navy-deep: #0f2f73;
    --navy-mid: #1e4ea6;
    --wire-light: #8fb4e6;
  }
  html, body {
    margin: 0;
    padding: 0;
    width: 1200px;
    height: 818px;
    overflow: hidden;
    background: var(--backdrop);
    font-family: "Roboto", Arial, sans-serif;
  }
  .canvas {
    position: relative;
    width: 1200px;
    height: 818px;
  }
  .business-card {
    position: absolute;
    left: 180px;
    top: 169px;
    width: 840px;
    height: 480px;
    background: var(--card-white);
    box-shadow: 0 14px 34px rgba(0,0,0,0.18);
    display: flex;
    overflow: hidden;
  }
  .artwork-panel {
    width: 300px;
    height: 100%;
    background:
      radial-gradient(ellipse at 70% 45%, var(--wire-light) 0%, rgba(143,180,230,0.35) 30%, rgba(30,78,166,0) 65%),
      linear-gradient(160deg, var(--navy-mid) 0%, var(--navy-deep) 100%);
  }
  .info-panel {
    position: relative;
    flex: 1;
    padding: 54px 0 0 48px;
  }
  .company-name {
    margin: 0;
    font-weight: 300;
    font-size: 38px;
    line-height: 1.02;
    color: var(--ink);
    letter-spacing: -0.5px;
  }
  .person-name {
    margin: 30px 0 0;
    font-weight: 300;
    font-size: 30px;
    color: var(--accent-blue);
    letter-spacing: -0.3px;
  }
  .contact-list {
    position: absolute;
    left: 48px;
    bottom: 46px;
    margin: 0;
    padding: 0;
    list-style: none;
    font-weight: 300;
    font-size: 22px;
    color: var(--ink);
    line-height: 1.28;
  }
  .contact-item {
    display: flex;
    align-items: center;
    gap: 12px;
  }
  .contact-icon {
    width: 14px;
    height: 14px;
    flex: none;
    fill: var(--ink);
  }
  .contact-item .faded { color: var(--ink-soft); }
</style>
</head>
<body>
<main class="canvas">
  <section class="business-card">
    <div class="artwork-panel" role="img" aria-label="Blue wireframe illustration of high-rise buildings"></div>
    <div class="info-panel">
      <h1 class="company-name">Valdrick Construction<br>Co Inc</h1>
      <p class="person-name">Dale Valdrick</p>
      <ul class="contact-list">
        <li class="contact-item">
          <svg class="contact-icon" viewBox="0 0 14 14" aria-hidden="true"><path d="M1 4c0-2 2-3 6-3s6 1 6 3v1h-3V4H4v1H1z M3 6h8l1 7H2z M7 8a1.6 1.6 0 1 0 0.01 0z"/></svg>
          <span>555-815-0926</span>
        </li>
        <li class="contact-item">
          <svg class="contact-icon" viewBox="0 0 14 14" aria-hidden="true"><path d="M1 3h12v8H1z M1.6 3.4L7 8l5.4-4.6" fill="none" stroke="#2a2a2a" stroke-width="1.4"/></svg>
          <span>dale1valdrick@norvexmail.com</span>
        </li>
        <li class="contact-item">
          <svg class="contact-icon" viewBox="0 0 14 14" aria-hidden="true"><path d="M7 1a4.2 4.2 0 0 0-4.2 4.2C2.8 8.4 7 13 7 13s4.2-4.6 4.2-7.8A4.2 4.2 0 0 0 7 1zm0 5.8a1.6 1.6 0 1 1 0-3.2 1.6 1.6 0 0 1 0 3.2z"/></svg>
          <span>4870 Quillford Lane Tallowmere <span class="faded">QR 55021</span></span>
        </li>
      </ul>
    </div>
  </section>
</main>
</body>
</html>
```